A start up Private Wine Label for export to Asia.

We are looking for the best graphic design for our very first wine label Corvessa Wines and would like the following requirements:

1. Black background - explore and play around the shade of black
2. Gold Shimmery Colour Font
3. Font should be a cursive classic posh that says Corvessa Wines
4. We would like the front graphic design to be simple and elegant and has a traditional classic feel to it.

Target Market(s)

Small scale to test the upper class market for export to Asia

Font styles to use
Script

Colors

Designer to choose colors to be used in the design.

Requirements
Must have
• Gold font for the label Corvessa Wines with shimmery touch to it.
• Elegant black background.
• Simple but elegant design.
• Attractive to the upper class market in Asia.
Nice to have
• Explore and play around with your imagination.

```html
<!DOCTYPE html>
<html lang="en">
<head>
<meta charset="utf-8">
<title>Corvessa Wines – Label</title>
<link rel="stylesheet" href="https://fonts.googleapis.com/css2?family=Pinyon+Script&display=swap">
<style>
  :root {
    --canvas: #ffffff;
    --gold-light: #f3e27a;
    --gold-mid: #d9b64e;
    --gold-deep: #a8772f;
    --black-panel: #070908;
    --black-gloss: #3d3b39;
    --wax-dark: #7d1414;
    --wax-mid: #a81e1e;
    --wax-glow: #e8601e;
    --ink: #1a1208;
  }
  html, body {
    margin: 0;
    padding: 0;
    width: 1200px;
    height: 1200px;
    overflow: hidden;
    background: var(--canvas);
  }
  .label-canvas {
    display: block;
    width: 1200px;
    height: 1200px;
  }
  .script {
    font-family: "Pinyon Script", cursive;
  }
  .brand-name { font-size: 104px; }
  .brand-word { font-size: 96px; }
  .band-text { font-size: 44px; fill: var(--ink); }
  .variety { font-size: 62px; }
</style>
</head>
<body>
<svg class="label-canvas" viewBox="0 0 1200 1200" xmlns="http://www.w3.org/2000/svg">
  <defs>
    <linearGradient id="goldFrame" x1="0" y1="0" x2="1" y2="0">
      <stop offset="0" stop-color="var(--gold-deep)"/>
      <stop offset="0.25" stop-color="var(--gold-mid)"/>
      <stop offset="0.5" stop-color="var(--gold-light)"/>
      <stop offset="0.75" stop-color="var(--gold-mid)"/>
      <stop offset="1" stop-color="var(--gold-deep)"/>
    </linearGradient>
    <linearGradient id="goldBand" x1="0" y1="0" x2="1" y2="0">
      <stop offset="0" stop-color="var(--gold-mid)"/>
      <stop offset="0.3" stop-color="var(--gold-light)"/>
      <stop offset="0.7" stop-color="var(--gold-light)"/>
      <stop offset="1" stop-color="var(--gold-deep)"/>
    </linearGradient>
    <linearGradient id="goldText" x1="0" y1="0" x2="1" y2="1">
      <stop offset="0" stop-color="var(--gold-deep)"/>
      <stop offset="0.35" stop-color="var(--gold-light)"/>
      <stop offset="0.6" stop-color="var(--gold-mid)"/>
      <stop offset="1" stop-color="var(--gold-deep)"/>
    </linearGradient>
    <linearGradient id="gloss" x1="0" y1="0" x2="1" y2="1">
      <stop offset="0" stop-color="var(--black-gloss)" stop-opacity="0.8"/>
      <stop offset="1" stop-color="var(--black-gloss)" stop-opacity="0.45"/>
    </linearGradient>
    <radialGradient id="wax" cx="0.5" cy="0.5" r="0.5">
      <stop offset="0" stop-color="var(--wax-glow)"/>
      <stop offset="0.45" stop-color="var(--wax-mid)"/>
      <stop offset="1" stop-color="var(--wax-dark)"/>
    </radialGradient>
    <clipPath id="panelClip">
      <path d="M422,88 H778 A64,60 0 0 0 842,148 V1052 A64,60 0 0 0 778,1112 H422 A64,60 0 0 0 358,1052 V148 A64,60 0 0 0 422,88 Z"/>
    </clipPath>
  </defs>

  <!-- frame -->
  <g class="label-frame">
    <path fill="url(#goldFrame)" d="M398,40 H802 A73,64 0 0 0 875,104 V1096 A73,64 0 0 0 802,1160 H398 A73,64 0 0 0 325,1096 V104 A73,64 0 0 0 398,40 Z"/>
    <path fill="none" stroke="var(--ink)" stroke-width="0.8" opacity="0.6" d="M404,47 H796 A70,62 0 0 0 868,109 V1091 A70,62 0 0 0 796,1153 H404 A70,62 0 0 0 332,1091 V109 A70,62 0 0 0 404,47 Z"/>
    <path fill="var(--gold-deep)" opacity="0.5" d="M414,80 H786 A66,62 0 0 0 852,140 V1060 A66,62 0 0 0 786,1120 H414 A66,62 0 0 0 348,1060 V140 A66,62 0 0 0 414,80 Z"/>
  </g>

  <!-- black panel -->
  <g class="label-panel" clip-path="url(#panelClip)">
    <rect x="358" y="88" width="484" height="1024" fill="var(--black-panel)"/>
    <path class="panel-gloss" fill="url(#gloss)" d="M358,88 H842 V200 Q560,360 358,688 Z"/>
  </g>

  <!-- bottle emblem -->
  <rect class="bottle-emblem" role="img" aria-label="Gold wine bottle emblem" x="570" y="136" width="60" height="248" rx="10" fill="url(#goldFrame)"/>

  <!-- brand title -->
  <line class="rule" x1="387" y1="480" x2="830" y2="480" stroke="var(--gold-mid)" stroke-width="0.8" opacity="0.5"/>
  <text class="script brand-name" x="600" y="570" text-anchor="middle" fill="url(#goldText)">Corvessa</text>
  <text class="script brand-word" x="624" y="706" text-anchor="middle" fill="url(#goldText)">Wine</text>
  <line class="rule" x1="387" y1="718" x2="830" y2="718" stroke="var(--gold-mid)" stroke-width="0.8" opacity="0.5"/>

  <!-- gold band with seal -->
  <rect class="gold-band" x="358" y="864" width="484" height="104" fill="url(#goldBand)"/>
  <text class="script band-text" x="432" y="930" text-anchor="middle">Since</text>
  <text class="script band-text" x="750" y="930" text-anchor="middle">xxxx</text>
  <circle class="wax-seal" role="img" aria-label="Red wax seal" cx="600" cy="912" r="92" fill="url(#wax)"/>

  <!-- variety -->
  <text class="script variety" x="600" y="1066" text-anchor="middle" fill="url(#goldText)">Wine Type</text>
</svg>
</body>
</html>
```